E learning Platform for privacy

Current website is as below and its more of a shell.
I need someone to take the text and content and design it properly.
https://study.vornaquill.com/

After that, design has to be implemented with elementor and wordpress
https://elementor.com/

```html
<!DOCTYPE html>
<html lang="en">
<head>
<meta charset="utf-8">
<title>Vorna Quill Learning Centre</title>
<link href="https://fonts.googleapis.com/css2?family=Audiowide&family=Roboto:ital,wght@0,400;0,500;0,700;1,400&display=swap" rel="stylesheet">
<style>
:root{
  --red:#e2491c;
  --amber:#ea811c;
  --brown:#8a6a4c;
  --cream:#fdf5ee;
  --ink:#1e1e1e;
  --grey:#666;
  --light:#f2f2f2;
  --white:#fff;
}
*{box-sizing:border-box;margin:0;padding:0}
html,body{width:1200px;height:4097px;overflow:hidden}
body{position:relative;font-family:"Roboto",sans-serif;color:var(--ink);background:var(--white)}
.abs{position:absolute}
.section-title{position:absolute;left:0;width:1200px;text-align:center;font-family:"Audiowide",sans-serif;font-weight:400;font-size:36px;color:var(--ink)}
.btn{position:absolute;display:flex;align-items:center;justify-content:center;gap:8px;background:var(--red);color:var(--white);border-radius:40px;font-weight:700;text-transform:uppercase}
.btn .dot{width:15px;height:15px;border-radius:50%;background:var(--white);display:inline-flex;align-items:center;justify-content:center}
.btn .dot::after{content:"";border-left:5px solid var(--red);border-top:4px solid transparent;border-bottom:4px solid transparent;margin-left:2px}

.hero{position:absolute;left:0;top:0;width:1200px;height:613px;background:var(--cream);overflow:hidden}
.logo{position:absolute;left:111px;top:36px;font-family:"Audiowide",sans-serif;font-size:36px;color:var(--red);letter-spacing:2px}
.logo small{display:block;font-family:"Roboto",sans-serif;font-size:7px;letter-spacing:5px;color:var(--ink);margin-top:-4px}
.nav{position:absolute;top:52px;font-size:15px;font-weight:500;color:var(--ink)}
.nav.active{color:var(--red)}
.nav.light{color:var(--white)}
.register{position:absolute;left:958px;top:40px;width:129px;height:43px;border-radius:24px;background:var(--white);color:var(--red);font-size:15px;font-weight:500;display:flex;align-items:center;justify-content:center}
.hero h1{position:absolute;left:109px;top:190px;font-family:"Audiowide",sans-serif;font-weight:400;font-size:52px;line-height:58px;color:#555;white-space:nowrap}
.hero h1 span{color:var(--red)}
.hero .lead{position:absolute;left:110px;top:330px;font-size:21px;line-height:30px;width:440px}

.course{position:absolute;top:813px;width:306px;height:325px;background:var(--white);box-shadow:0 2px 10px rgba(0,0,0,.1)}
.course .ph{height:188px}
.course h3{font-size:18px;font-weight:500;margin:22px 19px 10px}
.meta{font-size:14px;color:#444;display:flex;align-items:center;gap:8px;margin:0 19px 12px}
.ic{width:13px;height:13px;border-radius:50%;border:2px solid var(--red);display:inline-block}
.ic.sq{border-radius:2px}

.stats{position:absolute;left:0;top:1262px;width:1200px;height:239px;background:linear-gradient(90deg,var(--amber),var(--brown))}
.stat{position:absolute;top:36px;width:260px;margin-left:-130px;text-align:center;color:var(--white)}
.stat .ring{width:130px;height:130px;margin:0 auto;border-radius:50%;background:var(--white);border:5px solid rgba(255,255,255,.6);box-shadow:0 0 0 4px var(--white) inset;display:flex;flex-direction:column;align-items:center;justify-content:center}
.stat .num{font-size:24px;font-weight:700;color:#444;margin-top:4px}
.stat .label{font-size:21px;font-weight:500;margin-top:20px}

.mission{position:absolute;left:150px;top:1686px;width:900px;text-align:center;font-size:15px;line-height:28px;color:#555}
.feature{position:absolute;width:330px}
.feature h4{font-size:19px;font-weight:500;margin-bottom:16px}
.feature p{font-size:13px;line-height:22px;color:#555;text-align:justify}
.badge{position:absolute;width:102px;height:102px}

.testi{position:absolute;left:0;top:2441px;width:1200px;height:357px;background:var(--light)}
.arrow{position:absolute;width:36px;height:36px;border-radius:50%;background:#777;display:flex;align-items:center;justify-content:center}
.quote{position:absolute;left:407px;top:156px;width:560px;font-size:15px;font-style:italic;line-height:23px;color:#444}
.qmark{position:absolute;font-family:"Audiowide",sans-serif;font-size:54px;color:var(--amber)}

.post{position:absolute;top:2990px;width:311px}
.post .ph{height:210px}
.post .body{margin:0 16px;background:var(--white);box-shadow:0 4px 10px rgba(0,0,0,.08);padding:10px 20px 26px;height:162px;margin-top:-10px;position:relative}
.post h3{font-size:17px;font-weight:500;margin-bottom:14px}
.post .meta{margin:0 0 18px;gap:6px;font-size:14px}
.post p{font-size:15px;line-height:23px;color:#555;margin-bottom:14px}
.more{font-size:14px;font-weight:700;color:var(--red);display:flex;align-items:center;gap:6px}
.more .ic{width:13px;height:13px;background:var(--red);border:none}

.footer{position:absolute;left:0;top:3645px;width:1200px;height:452px;background:linear-gradient(90deg,var(--brown),var(--amber))}
.join{position:absolute;left:111px;top:3501px;width:978px;height:204px;background:var(--white);border-radius:100px;box-shadow:0 6px 18px rgba(0,0,0,.12);text-align:center}
.join h2{font-family:"Audiowide",sans-serif;font-weight:400;font-size:36px;margin-top:28px}
.join p{font-size:15px;color:#555;margin-top:10px}
.fhead{position:absolute;font-size:18px;font-weight:500;color:var(--white)}
.flink{position:absolute;left:372px;font-size:14px;color:var(--white)}
.flink::before{content:"»";margin-right:10px}
.ftext{position:absolute;font-size:14px;line-height:24px;color:var(--white)}
.social{position:absolute;top:3869px;width:36px;height:36px;border-radius:50%;border:2px solid var(--white)}
.email{position:absolute;left:847px;top:3863px;width:240px;height:46px;background:var(--white);border-radius:3px;font-size:14px;color:#555;padding:14px 18px}
.copy{position:absolute;left:0;top:4038px;width:1200px;text-align:center;font-size:15px;color:var(--white)}
</style>
</head>
<body>

<header class="hero">
  <svg class="abs" style="left:0;top:0" width="1200" height="613" aria-hidden="true">
    <defs><linearGradient id="heroShape" x1="0" y1="1" x2="1" y2="0"><stop offset="0" stop-color="#c8772a"/><stop offset="1" stop-color="#5a4634"/></linearGradient></defs>
    <path d="M890 0 L1200 0 L1200 180 L870 613 Q760 622 660 560 Q560 480 600 360 Z" fill="url(#heroShape)"/>
  </svg>
  <div class="abs" role="img" aria-label="Isometric illustration of a learner working at a desk with a computer, books and a lamp" style="left:640px;top:150px;width:450px;height:440px;border-radius:30px;background:linear-gradient(135deg,#dcd8f6,#f1e2ea 60%,#f6c9d6)"></div>

  <div class="logo">VQLC<small>LEARNING CENTRE</small></div>
  <div class="nav active" style="left:438px">Home</div>
  <div class="nav" style="left:505px">Blogs</div>
  <div class="nav" style="left:572px">Courses</div>
  <div class="nav" style="left:655px">Contact Us</div>
  <div class="nav" style="left:758px">About Us</div>
  <div class="nav light" style="left:848px">➜ Sign In</div>
  <div class="register">Register</div>

  <h1><span>Vorna Quill</span><br>Learning Centre</h1>
  <p class="lead">Largest online e-learning resource for data protection &amp; privacy</p>
  <div class="btn" style="left:111px;top:427px;width:223px;height:58px;font-size:20px">Get Trained <span class="dot"></span></div>
</header>

<h2 class="section-title" style="top:728px">Featured Courses</h2>

<article class="course" style="left:111px">
  <div class="ph" role="img" aria-label="Photo of a smiling student with headphones" style="background:linear-gradient(135deg,#e9e4dc,#c9584c)"></div>
  <h3>How to Scale Social Impact</h3>
  <div class="meta"><span class="ic"></span>By Admin</div>
  <div class="meta"><span class="ic"></span>55 Weeks &nbsp;|&nbsp; <span class="ic sq"></span>Feb 20, 2020</div>
</article>
<article class="course" style="left:447px">
  <div class="ph" role="img" aria-label="Photo of a woman working on a laptop" style="background:linear-gradient(135deg,#2c3440,#8d8f96)"></div>
  <h3>Global Social Entrepreneurship</h3>
  <div class="meta"><span class="ic"></span>By Admin</div>
  <div class="meta"><span class="ic"></span>107 Weeks &nbsp;|&nbsp; <span class="ic sq"></span>Feb 20, 2020</div>
</article>
<article class="course" style="left:783px">
  <div class="ph" role="img" aria-label="Photo of a woman with glasses at a laptop in a café" style="background:linear-gradient(135deg,#5a3a2c,#b99a7c)"></div>
  <h3>Open Demonstration Course</h3>
  <div class="meta"><span class="ic"></span>By Admin</div>
  <div class="meta"><span class="ic"></span>81 Weeks &nbsp;|&nbsp; <span class="ic sq"></span>Feb 20, 2020</div>
</article>

<section class="stats">
  <div class="stat" style="left:193px"><div class="ring">
    <svg width="40" height="30" viewBox="0 0 40 30" fill="none" stroke="#e2491c" stroke-width="2"><circle cx="20" cy="8" r="5"/><circle cx="8" cy="10" r="4"/><circle cx="32" cy="10" r="4"/><path d="M10 28 Q20 12 30 28 M1 24 Q8 14 14 20 M39 24 Q32 14 26 20"/></svg>
    <div class="num">6,375</div></div><div class="label">Enrolled Students</div></div>
  <div class="stat" style="left:455px"><div class="ring">
    <svg width="40" height="32" viewBox="0 0 40 32" fill="none" stroke="#e2491c" stroke-width="2"><path d="M2 4 H18 Q20 4 20 6 V30 M38 4 H22 Q20 4 20 6 M2 4 V28 H18 M38 4 V28 H22 M6 10 H16 M6 15 H16 M6 20 H16 M24 10 H34 M24 15 H34 M24 20 H34"/></svg>
    <div class="num">114</div></div><div class="label">Lessons</div></div>
  <div class="stat" style="left:716px"><div class="ring">
    <svg width="40" height="32" viewBox="0 0 40 32" fill="none" stroke="#e2491c" stroke-width="2"><rect x="2" y="2" width="36" height="28"/><path d="M2 8 H38 M2 24 H38 M16 11 L25 16 L16 21 Z"/></svg>
    <div class="num">169</div></div><div class="label">Videos</div></div>
  <div class="stat" style="left:979px"><div class="ring">
    <svg width="40" height="34" viewBox="0 0 40 34" fill="none" stroke="#e2491c" stroke-width="2"><rect x="2" y="2" width="34" height="24"/><rect x="6" y="6" width="26" height="16"/><circle cx="28" cy="24" r="5"/><path d="M25 28 L24 33 L28 31 L32 33 L31 28"/></svg>
    <div class="num">2,586</div></div><div class="label">Certificate Programme</div></div>
</section>

<h2 class="section-title" style="top:1616px">Why the (VQLC) Learning Centre?</h2>
<p class="mission">Our mission at the Vorna Quill Learning Centre (VQLC) is to provide business and job opportunities,as well as to enhance personal and career advancement for data protection / privacy professionals.</p>

<svg width="0" height="0" style="position:absolute" aria-hidden="true">
  <defs><path id="shieldShape" d="M51 6 Q96 10 96 40 Q96 82 51 96 Q6 82 6 40 Q6 10 51 6 Z"/></defs>
</svg>

<svg class="badge" style="left:111px;top:1790px" viewBox="0 0 102 102" aria-hidden="true"><use href="#shieldShape" fill="#e2491c"/><circle cx="51" cy="46" r="20" fill="none" stroke="#fff" stroke-width="2"/><circle cx="51" cy="46" r="6" fill="none" stroke="#fff" stroke-width="2"/></svg>
<div class="feature" style="left:239px;top:1786px"><h4>Comprehensive Roadmap</h4><p>Our objective is to provide a comprehensive competency roadmap, instead of one-off courses, whether you are a new or experienced officer,</p></div>

<svg class="badge" style="left:641px;top:1790px" viewBox="0 0 102 102" aria-hidden="true"><use href="#shieldShape" fill="#fff" style="filter:drop-shadow(0 3px 4px rgba(0,0,0,.15))"/><circle cx="51" cy="46" r="18" fill="none" stroke="#ea811c" stroke-width="2" stroke-dasharray="5 3"/><circle cx="51" cy="46" r="8" fill="none" stroke="#444" stroke-width="2"/></svg>
<div class="feature" style="left:770px;top:1786px;width:319px"><h4>Operational Perspective</h4><p>We cover a broad range of data protection topics from both a legal and operational perspective, covering multiple jurisdictions</p></div>

<svg class="badge" style="left:111px;top:1944px" viewBox="0 0 102 102" aria-hidden="true"><use href="#shieldShape" fill="#fff" style="filter:drop-shadow(0 3px 4px rgba(0,0,0,.15))"/><rect x="38" y="28" width="22" height="30" fill="none" stroke="#444" stroke-width="2"/><path d="M42 36 H56 M42 42 H56 M42 48 H52" stroke="#ea811c" stroke-width="2"/><path d="M64 28 V56" stroke="#ea811c" stroke-width="3"/></svg>
<div class="feature" style="left:239px;top:1940px"><h4>Academic &amp; International Certification</h4><p>We partner with prominent universities in the region as well as international certification bodies such as the International Association</p></div>

<svg class="badge" style="left:641px;top:1944px" viewBox="0 0 102 102" aria-hidden="true"><use href="#shieldShape" fill="#fff" style="filter:drop-shadow(0 3px 4px rgba(0,0,0,.15))"/><circle cx="51" cy="34" r="4" fill="none" stroke="#444" stroke-width="2"/><path d="M45 60 V44 H57 V60" fill="none" stroke="#444" stroke-width="2"/><path d="M34 30 L40 36 M68 30 L62 36 M34 62 L40 56 M68 62 L62 56" stroke="#ea811c" stroke-width="2"/></svg>
<div class="feature" style="left:770px;top:1940px;width:319px"><h4>Modular Approach &amp; Flexibility</h4><p>All our courses are modular in nature to cater to the busy professional, meaning that you can take the courses separately first at your own pace</p></div>

<svg class="badge" style="left:111px;top:2098px" viewBox="0 0 102 102" aria-hidden="true"><use href="#shieldShape" fill="#fff" style="filter:drop-shadow(0 3px 4px rgba(0,0,0,.15))"/><circle cx="40" cy="34" r="4" fill="none" stroke="#444" stroke-width="2"/><circle cx="62" cy="38" r="4" fill="none" stroke="#444" stroke-width="2"/><circle cx="50" cy="58" r="4" fill="none" stroke="#ea811c" stroke-width="2"/><path d="M42 37 L48 55 M60 41 L52 55 M44 34 L58 37" stroke="#444" stroke-width="1.5"/></svg>
<div class="feature" style="left:239px;top:2094px"><h4>Network with other peers</h4><p>Participate in our online communities and discussion rooms and your network with other like-minded course participants</p></div>

<svg class="badge" style="left:641px;top:2098px" viewBox="0 0 102 102" aria-hidden="true"><use href="#shieldShape" fill="#fff" style="filter:drop-shadow(0 3px 4px rgba(0,0,0,.15))"/><rect x="38" y="40" width="26" height="18" rx="2" fill="none" stroke="#444" stroke-width="2"/><path d="M46 40 V36 H56 V40 M38 48 H64" stroke="#444" stroke-width="2" fill="none"/><path d="M34 30 V26 M68 30 V26 M51 30 V24" stroke="#ea811c" stroke-width="2"/></svg>
<div class="feature" style="left:770px;top:2094px;width:319px"><h4>Business and Job Opportunities</h4><p>Collaborate with other professionals on potential business opportunities whether it relates to consultancy, legal or training services.</p></div>

<div class="btn" style="left:506px;top:2263px;width:188px;height:57px;font-size:15px">Learn More <span class="dot"></span></div>

<section class="testi">
  <h2 class="section-title" style="top:66px">What Peoples Say</h2>
  <div class="arrow" style="left:111px;top:172px"><svg width="16" height="10" viewBox="0 0 16 10"><path d="M15 5 H2 M6 1 L2 5 L6 9" stroke="#fff" stroke-width="2" fill="none"/></svg></div>
  <div class="arrow" style="left:1053px;top:172px"><svg width="16" height="10" viewBox="0 0 16 10"><path d="M1 5 H14 M10 1 L14 5 L10 9" stroke="#fff" stroke-width="2" fill="none"/></svg></div>
  <div class="abs" role="img" aria-label="Portrait photo of the reviewer" style="left:237px;top:143px;width:106px;height:106px;border-radius:50%;background:linear-gradient(160deg,#6fb0d8,#2f6f9c)"></div>
  <div class="qmark" style="left:354px;top:120px">“</div>
  <p class="quote">Lorem ipsum dolor sit amet, consectetur adipiscing elit, sed do eiusmod tempor incididunt ut labore et dolore magna aliqua. Ut enim ad minim veniam, quis nostrud exercitation ullamco laboris nisi ut aliquip ex ea commodo consequat.</p>
  <div class="qmark" style="left:894px;top:196px">”</div>
  <div class="abs" style="left:407px;top:248px;font-size:17px;font-weight:500">John Doe</div>
  <div class="abs" style="left:407px;top:273px;font-size:12px;color:#555">Company Name</div>
</section>

<h2 class="section-title" style="top:2910px">Our Blog</h2>

<article class="post" style="left:111px">
  <div class="ph" role="img" aria-label="Photo of a woman writing beside a laptop and plants" style="background:linear-gradient(135deg,#e7e2dc,#6e7060)"></div>
  <div class="body"><h3>Sed ut perspiciatis unde omnis</h3>
  <div class="meta"><span class="ic"></span>by Admin &nbsp;&nbsp; <span class="ic sq"></span>Jan 10, 2020</div>
  <p>Lorem ipsum dolor sit consectetur adipiscing elit, sed do eiusmod</p>
  <div class="more">READ MORE <span class="ic"></span></div></div>
</article>
<article class="post" style="left:446px">
  <div class="ph" role="img" aria-label="Photo of a tall stack of books on a table" style="background:linear-gradient(135deg,#3b3a34,#c9c6bc)"></div>
  <div class="body"><h3>Sed ut perspiciatis unde omnis</h3>
  <div class="meta"><span class="ic"></span>by Admin &nbsp;&nbsp; <span class="ic sq"></span>Dec 27, 2019</div>
  <p>Lorem ipsum dolor sit consectetur adipiscing elit, sed do eiusmod</p>
  <div class="more">READ MORE <span class="ic"></span></div></div>
</article>
<article class="post" style="left:778px">
  <div class="ph" role="img" aria-label="Photo of a student with headphones studying at a laptop" style="background:linear-gradient(135deg,#3a4a5a,#d9c4a8)"></div>
  <div class="body"><h3>Sed ut perspiciatis unde omnis</h3>
  <div class="meta"><span class="ic"></span>by Admin &nbsp;&nbsp; <span class="ic sq"></span>Dec 18, 2019</div>
  <p>Lorem ipsum dolor sit consectetur adipiscing elit, sed do eiusmod</p>
  <div class="more">READ MORE <span class="ic"></span></div></div>
</article>

<footer class="footer"></footer>

<section class="join">
  <h2>Join Us</h2>
  <p>Sed ut perspiciatis unde omnis iste natus error sit voluptatem accusantium doloremque laudantium,aperiam,</p>
</section>
<div class="btn" style="left:517px;top:3625px;width:166px;height:50px;font-size:14px">Join Now <span class="dot"></span></div>

<div class="abs" style="left:134px;top:3778px;font-family:'Audiowide',sans-serif;font-size:36px;color:var(--white);letter-spacing:2px">VQLC</div>
<div class="abs" style="left:146px;top:3822px;font-size:7px;letter-spacing:5px;color:var(--white)">LEARNING CENTRE</div>
<div class="social" style="left:124px"></div>
<div class="social" style="left:170px"></div>
<div class="social" style="left:216px"></div>
<div class="social" style="left:261px"></div>

<div class="fhead" style="left:372px;top:3760px">QUICK LINKS</div>
<div class="flink" style="top:3806px">Home</div>
<div class="flink" style="top:3835px">Blogs</div>
<div class="flink" style="top:3865px">Courses</div>
<div class="flink" style="top:3894px">Contact Us</div>
<div class="flink" style="top:3923px">About Us</div>

<div class="fhead" style="left:576px;top:3760px">CONTACT US</div>
<svg class="abs" style="left:580px;top:3808px" width="10" height="14" viewBox="0 0 10 14"><path d="M5 13 C1 8 0 6 0 5 A5 5 0 0 1 10 5 C10 6 9 8 5 13 Z" fill="#fff"/><circle cx="5" cy="5" r="2" fill="#a46e40"/></svg>
<div class="ftext" style="left:606px;top:3802px">418 Harlow Ave, Brenton,<br>TX 75410, USA</div>
<svg class="abs" style="left:581px;top:3866px" width="8" height="12" viewBox="0 0 8 12"><rect x="1" y="1" width="6" height="10" rx="1" fill="none" stroke="#fff" stroke-width="1.5"/></svg>
<div class="ftext" style="left:606px;top:3860px">+1 (800) 555 01 42</div>
<svg class="abs" style="left:579px;top:3900px" width="13" height="12" viewBox="0 0 13 12"><rect x="1" y="3" width="11" height="8" fill="none" stroke="#fff" stroke-width="1.5"/><rect x="3" y="0.5" width="7" height="3" fill="#fff"/></svg>
<div class="ftext" style="left:606px;top:3894px">555 274 9031</div>
<svg class="abs" style="left:578px;top:3935px" width="14" height="11" viewBox="0 0 14 11"><rect x="1" y="1" width="12" height="9" fill="none" stroke="#fff" stroke-width="1.5"/><path d="M1 1 L7 6 L13 1" fill="none" stroke="#fff" stroke-width="1.5"/></svg>
<div class="ftext" style="left:606px;top:3928px">info@study.vornaquill.com</div>

<div class="fhead" style="left:845px;top:3761px">Newsletter</div>
<div class="ftext" style="left:846px;top:3802px;font-size:13px">Lorem ipsum dolor sit, consectetur<br>adipiscing elit</div>
<div class="email">Your Email</div>
<div class="btn" style="left:845px;top:3931px;width:121px;height:45px;font-size:14px">Submit</div>

<div class="abs" style="left:0;top:4007px;width:1200px;height:1px;background:rgba(255,255,255,.35)"></div>
<div class="copy">(c) 2020 study.vornaquill.com &nbsp;| All Rights Reserved</div>

</body>
</html>
```